Corvane Card

The logo is the Spanish flag colors I want a vibrant eye catching design with the yellow / red colors over either Navy or white background or black even ,
Would like a 2D feel to the logo with another lighter color logo under it look ,

Contact Information for Business Card

Corvane Flooring
Teodor Vashkin
Main Number
Cell Number
Fax Number

Website on the side of the card somewhere

Font styles to use
Sans Serif

Colors
ec1f27
ffc214

Requirements
Must have
• 2 logos feel one is bolder and the other one underneath very light

```html
<!DOCTYPE html>
<html lang="en">
<head>
<meta charset="utf-8">
<title>Corvane Card</title>
<link rel="stylesheet" href="https://fonts.googleapis.com/css2?family=Michroma&family=Arimo:wght@400&display=swap">
<style>
  :root {
    --brand-red: #ec1f27;
    --brand-yellow: #ffc214;
    --card-light: #f0ebe9;
    --page-bg: #e4e1df;
  }
  * { margin: 0; padding: 0; box-sizing: border-box; }
  html, body { width: 1200px; height: 900px; overflow: hidden; }
  body {
    background: var(--page-bg);
    position: relative;
  }
  .business-card {
    position: absolute;
    left: 100px;
    top: 140px;
    width: 1000px;
    height: 620px;
    display: flex;
    box-shadow: 0 10px 30px rgba(0,0,0,0.15);
  }
  .brand-panel {
    width: 505px;
    height: 100%;
    background: var(--card-light);
    display: flex;
    flex-direction: column;
    align-items: center;
    justify-content: center;
    gap: 18px;
  }
  .brand-mark {
    width: 64px;
    height: 64px;
    background: var(--brand-yellow);
    border-radius: 6px;
  }
  .brand-name {
    font-family: "Michroma", sans-serif;
    color: var(--brand-red);
    text-align: center;
    line-height: 1.25;
  }
  .brand-name .brand-word { display: block; font-size: 44px; letter-spacing: 1px; }
  .brand-name .brand-trade { display: block; font-size: 26px; letter-spacing: 14px; margin-right: -14px; }
  .panel-divider {
    width: 8px;
    height: 100%;
    background: var(--brand-yellow);
  }
  .contact-panel {
    flex: 1;
    background: var(--brand-red);
    position: relative;
  }
  .person-name {
    position: absolute;
    left: 58px;
    top: 120px;
    font-family: "Michroma", sans-serif;
    font-size: 28px;
    color: var(--brand-yellow);
    letter-spacing: 0.5px;
    white-space: nowrap;
  }
  .contact-list {
    position: absolute;
    left: 58px;
    top: 320px;
    list-style: none;
  }
  .contact-item {
    display: flex;
    align-items: center;
    height: 36.5px;
    font-family: "Arimo", sans-serif;
    font-size: 27px;
    color: #ffffff;
    white-space: nowrap;
  }
  .contact-icon {
    width: 26px;
    height: 26px;
    margin-right: 10px;
    fill: var(--brand-yellow);
    flex-shrink: 0;
  }
</style>
</head>
<body>
  <div class="business-card">
    <section class="brand-panel">
      <div class="brand-mark"></div>
      <div class="brand-name">
        <span class="brand-word">CORVANE</span>
        <span class="brand-trade">FLOORING</span>
      </div>
    </section>
    <div class="panel-divider"></div>
    <section class="contact-panel">
      <h1 class="person-name">TEODOR VASHKIN</h1>
      <ul class="contact-list">
        <li class="contact-item">
          <svg class="contact-icon" viewBox="0 0 26 26" aria-hidden="true"><path d="M2 10c0-4 5-6 11-6s11 2 11 6v2h-6v-3H8v3H2z"/><rect x="5" y="13" width="16" height="9" rx="2"/></svg>
          410 276 3190
        </li>
        <li class="contact-item">
          <svg class="contact-icon" viewBox="0 0 26 26" aria-hidden="true"><path d="M8 1h10a2 2 0 0 1 2 2v20a2 2 0 0 1-2 2H8a2 2 0 0 1-2-2V3a2 2 0 0 1 2-2zm1 3v15h8V4z"/><circle cx="13" cy="22" r="1.3" fill="#ec1f27"/></svg>
          410 276 3194
        </li>
        <li class="contact-item">
          <svg class="contact-icon" viewBox="0 0 26 26" aria-hidden="true"><rect x="7" y="2" width="12" height="6"/><path d="M3 9h20a2 2 0 0 1 2 2v8h-5v-4H6v4H1v-8a2 2 0 0 1 2-2z"/><rect x="7" y="16" width="12" height="8"/></svg>
          410 276 3198
        </li>
        <li class="contact-item">
          <svg class="contact-icon" viewBox="0 0 26 26" aria-hidden="true"><path d="M2 6h22v14H2z M4 8l9 7 9-7" stroke="#ec1f27" stroke-width="1.5"/></svg>
          hello@corvaneflooring.com
        </li>
        <li class="contact-item">
          <svg class="contact-icon" viewBox="0 0 26 26" aria-hidden="true"><circle cx="13" cy="13" r="11"/><path d="M8 7c3 1 4 3 3 5s1 4 3 4-1 4-3 5M17 5c-1 2 0 4 3 4" stroke="#ec1f27" stroke-width="1.6" fill="none"/></svg>
          www.corvaneflooring.com
        </li>
      </ul>
    </section>
  </div>
</body>
</html>
```